Personal Web page for recruiter and owner of consulting firm

I work full time as a recruiter so I want a page that allows for me to support my efforts. I would like a long single page, I need to be able to upload four two minute videos, and 4 images. I also want the color scheme to match with my consulting company. I own the domain marcusfenwold.net already through wordpress . I took a shot at it myself and its terrible.

Target Market(s)

Potential clients

Industry/Entity Type

Management Consulting

Logo Text

marcus fenwold

Font styles to use
Serif

Requirements
Must have
• Must in color scheme go well with my consulting company logo attached
• Must be able to upload 4 two minute videos and 4 images (photos of me)
• Single long scroll page
• Modern and clean
Nice to have
• Easy for me to update videos images and text without complex coding
Should not have
• I want the design and feel to go well with my logos not exactly replicate it

```html
<!DOCTYPE html>
<html lang="en">
<head>
<meta charset="utf-8">
<title>Marcus Fenwold – Recruiter &amp; Consultant</title>
<link rel="stylesheet" href="https://fonts.googleapis.com/css2?family=Open+Sans:ital,wght@0,300;0,400;0,600;1,400&display=swap">
<style>
:root{
  --navy:#2f4a85;
  --navy-dark:#253c6e;
  --ink:#333333;
  --muted:#8a8a8a;
  --charcoal:#3f3f3f;
  --pale:#f4f4f9;
  --footer:#44453f;
  --footer-line:#5a5b55;
  --footer-text:#d8d8d2;
  --white:#ffffff;
}
*{box-sizing:border-box;margin:0;padding:0}
html,body{width:1200px;height:2975px;overflow:hidden}
body{position:relative;font-family:"Open Sans",Arial,sans-serif;color:var(--ink);background:var(--white)}
h1,h2,h3,h4{font-weight:400}
.abs{position:absolute}

/* header */
.site-header{position:absolute;left:0;top:0;width:1200px;height:93px;background:var(--white);border-top:3px solid var(--navy-dark)}
.brand{position:absolute;left:135px;top:27px;font-size:22px;font-weight:400;color:var(--ink);letter-spacing:1px;white-space:nowrap}
.main-nav{position:absolute;top:62px;left:0;width:1200px;font-size:12px;color:#222}
.main-nav span{position:absolute;white-space:nowrap}
.main-nav .active{color:var(--navy)}
.main-nav .active::after{content:"";position:absolute;left:-3px;right:-3px;top:28px;height:2px;background:var(--navy)}
.search-icon{position:absolute;left:1047px;top:20px}

/* hero */
.hero{position:absolute;left:0;top:93px;width:1200px;height:456px;background:linear-gradient(90deg,#dfe3e8 0%,#c9d1d9 45%,#d7dde3 100%)}
.hero-photo{position:absolute;left:640px;top:0;width:440px;height:456px;background:radial-gradient(ellipse at 50% 35%,#c99a82 0%,#b7917d 18%,#e9eaec 45%,rgba(215,221,227,0) 75%)}
.hero-title{position:absolute;left:133px;top:112px;font-size:58px;font-weight:300;color:#1f1f1f;letter-spacing:.5px}
.hero-sub{position:absolute;left:135px;top:202px;font-size:14px;color:#222}
.btn{position:absolute;display:flex;align-items:center;justify-content:center;border-radius:24px;font-size:12px;font-weight:600;text-transform:uppercase;color:var(--white);background:var(--navy)}
.btn-sm{font-size:10px;font-weight:400;text-transform:none;border-radius:16px}
.btn-outline{background:var(--white);color:#444;border:1px solid #888}
.dots{position:absolute;left:134px;top:342px;display:flex;gap:8px}
.dots i{width:7px;height:7px;border-radius:50%;background:#c5ccd6}
.dots i.on{background:var(--navy)}

/* section titles */
.section-title{position:absolute;left:0;width:1200px;text-align:center;font-size:35px;font-weight:300;color:#444}

/* services */
.service-icon{position:absolute;width:104px;height:104px;border-radius:50%;display:flex;align-items:center;justify-content:center}
.service-name{position:absolute;width:300px;text-align:center;font-size:19px;font-weight:400;color:#222}
.service-text{position:absolute;width:270px;text-align:center;font-size:11.5px;line-height:21px;color:var(--muted)}

/* about */
.about{position:absolute;left:0;top:1065px;width:1200px;height:426px;background:var(--pale)}
.about-title{position:absolute;left:133px;top:54px;font-size:34px;font-weight:300;color:#333}
.about-lead{position:absolute;left:133px;top:115px;width:460px;font-size:12.5px;font-style:italic;line-height:22px;color:#555}
.about-list{position:absolute;left:133px;top:176px;list-style:none;font-size:12.5px;color:var(--navy)}
.about-list li{height:22.5px;padding-left:22px;position:relative}
.about-list li::before{content:"›";position:absolute;left:2px;top:-2px;font-size:15px;color:#333}
.video-frame{position:absolute;left:662px;top:63px;width:410px;height:266px;border:5px solid var(--white);box-shadow:0 0 0 1px #dcdce4}
.video-fill{width:100%;height:100%;background:linear-gradient(180deg,#c6d1dc 0%,#9fb0c0 60%,#8a9aaa 100%)}
.play{position:absolute;border-radius:50%;background:rgba(255,255,255,.55);border:2px solid rgba(60,60,60,.7)}

/* growth band */
.growth{position:absolute;left:0;top:1491px;width:1200px;height:438px;background:linear-gradient(160deg,#4a4a4a 0%,#3a3a3a 45%,#2c2c2c 100%)}
.growth-title{position:absolute;left:0;top:100px;width:1200px;text-align:center;font-size:47px;font-weight:300;color:var(--white)}
.growth-text{position:absolute;left:130px;top:195px;width:940px;text-align:center;font-size:11.5px;line-height:22px;color:#dddddd}

/* testimonials */
.client-photo{position:absolute;width:147px;height:133px;background:linear-gradient(180deg,#b7b3ad 0%,#a58c7c 60%,#6c5e55 100%)}
.quote{position:absolute;width:268px;font-size:12px;line-height:23px;color:#555;text-align:justify}
.quote-by{position:absolute;font-size:12px;font-style:italic;color:var(--navy)}
.divider{position:absolute;left:133px;top:2288px;width:934px;height:1px;background:#e2e2e2}

/* blog */
.blog-thumb{position:absolute;width:297px;height:161px}
.blog-title{position:absolute;font-size:14px;font-weight:400;color:#333}
.blog-date{position:absolute;font-size:10px;color:var(--muted)}

/* footer */
.site-footer{position:absolute;left:0;top:2677px;width:1200px;height:298px;background:var(--footer)}
.footer-col{position:absolute;top:0;width:184px}
.footer-col h4{position:absolute;top:39px;font-size:17px;font-weight:400;color:var(--white);white-space:nowrap}
.footer-col hr{position:absolute;top:86px;width:184px;border:0;border-top:1px solid var(--footer-line)}
.footer-col ul{position:absolute;top:103px;list-style:none;font-size:11px;color:var(--footer-text);white-space:nowrap}
.footer-col li{height:22.4px;display:flex;align-items:center;gap:12px}
.footer-rule{position:absolute;left:133px;top:242px;width:934px;border:0;border-top:1px solid var(--footer-line)}
.copyright{position:absolute;left:0;top:261px;width:1200px;text-align:center;font-size:11px;color:var(--footer-text)}
</style>
</head>
<body>

<header class="site-header">
  <div class="brand">Fenwold Strategies</div>
  <svg class="search-icon" width="22" height="22" viewBox="0 0 22 22" fill="none" stroke="#888" stroke-width="1.8"><circle cx="9" cy="9" r="7"/><line x1="14" y1="14" x2="20" y2="20"/></svg>
  <nav class="main-nav">
    <span class="active" style="left:571px">HOME</span>
    <span style="left:641px">ABOUT US</span>
    <span style="left:740px">SERVICES</span>
    <span style="left:832px">NEWS</span>
    <span style="left:906px">CLIENTS</span>
    <span style="left:992px">CONTACT US</span>
  </nav>
</header>

<section class="hero">
  <div class="hero-photo" role="img" aria-label="Portrait of a smiling recruiter in a white blouse in front of a blurred office"></div>
  <h1 class="hero-title">Full time recruiter</h1>
  <p class="hero-sub">Lorem ipsum dolor sit amet, consectetur adipiscing elit</p>
  <a class="btn" style="left:135px;top:258px;width:186px;height:48px">Get started now</a>
  <div class="dots"><i class="on"></i><i></i><i></i></div>
</section>

<section class="services">
  <h2 class="section-title" style="top:596px">Our Services</h2>

  <div class="service-icon" style="left:212px;top:668px;background:var(--navy)">
    <svg width="44" height="38" viewBox="0 0 44 38"><rect x="14" y="2" width="16" height="8" rx="2" fill="none" stroke="#fff" stroke-width="3"/><rect x="2" y="9" width="40" height="27" rx="3" fill="#fff"/><rect x="2" y="19" width="40" height="2" fill="#2f4a85"/><rect x="19" y="16" width="6" height="8" fill="#fff" stroke="#2f4a85" stroke-width="1.5"/></svg>
  </div>
  <div class="service-icon" style="left:549px;top:668px;background:var(--charcoal)">
    <svg width="50" height="40" viewBox="0 0 50 40" fill="#fff"><circle cx="25" cy="9" r="7"/><path d="M13 34c0-9 5-14 12-14s12 5 12 14z"/><circle cx="10" cy="14" r="5"/><path d="M1 34c0-7 4-11 9-11 2 0 3 .5 4 1-2 3-3 6-3 10z"/><circle cx="40" cy="14" r="5"/><path d="M49 34c0-7-4-11-9-11-2 0-3 .5-4 1 2 3 3 6 3 10z"/></svg>
  </div>
  <div class="service-icon" style="left:882px;top:668px;background:var(--charcoal)">
    <svg width="46" height="38" viewBox="0 0 46 38"><polyline points="3,2 3,35 44,35" fill="none" stroke="#fff" stroke-width="3"/><path d="M6 32 L14 16 L22 24 L32 8 L42 20 L42 32 Z" fill="#fff"/></svg>
  </div>

  <h3 class="service-name" style="left:114px;top:803px">Recruiter</h3>
  <h3 class="service-name" style="left:451px;top:803px">Consulting</h3>
  <h3 class="service-name" style="left:784px;top:803px">Strategies</h3>

  <p class="service-text" style="left:130px;top:847px">Neque porro quisquam est, qui dolorem ipsum quia dolor sit amet, consectetur, adipisci velit, sed quia non numquam eius modi</p>
  <p class="service-text" style="left:467px;top:847px">Neque porro quisquam est, qui dolorem ipsum quia dolor sit amet, consectetur, adipisci velit, sed quia non numquam eius modi</p>
  <p class="service-text" style="left:800px;top:847px">Neque porro quisquam est, qui dolorem ipsum quia dolor sit amet, consectetur, adipisci velit, sed quia non numquam eius modi</p>

  <a class="btn btn-sm" style="left:217px;top:939px;width:96px;height:33px">Learn More</a>
  <a class="btn btn-sm btn-outline" style="left:551px;top:939px;width:96px;height:33px">Learn More</a>
  <a class="btn btn-sm btn-outline" style="left:885px;top:939px;width:96px;height:33px">Learn More</a>
</section>

<section class="about">
  <h2 class="about-title">About us</h2>
  <p class="about-lead">Lorem ipsum dolor sit amet, consectetur adipiscing elit, sed do eiusmod tempor incididunt ut labore et dolore magna aliqua.</p>
  <ul class="about-list">
    <li>Lorem ipsum dolor sit amet, consectetur</li>
    <li>Nemo enim ipsam voluptatem quia voluptas sit</li>
    <li>Sed ut perspiciatis unde omnis</li>
    <li>Ut enim ad minima veniam, quis nostrum</li>
  </ul>
  <a class="btn btn-sm" style="left:133px;top:295px;width:96px;height:33px">Learn More</a>
  <div class="video-frame">
    <div class="video-fill" role="img" aria-label="Video still: hand presenting floating screens with candidate profiles"></div>
    <div class="play" style="left:172px;top:98px;width:56px;height:56px"></div>
    <svg class="abs" style="left:193px;top:114px" width="20" height="24" viewBox="0 0 20 24"><path d="M2 2 L18 12 L2 22 Z" fill="#333"/></svg>
  </div>
</section>

<section class="growth" role="img" aria-label="Dark photo of a desk with a laptop, coffee cup and phone">
  <h2 class="growth-title">Entrepreneurs and facilitating growth</h2>
  <p class="growth-text">Nemo enim ipsam voluptatem quia voluptas sit aspernatur aut odit aut fugit, sed quia consequuntur magni dolores eos qui ratione voluptatem sequi nesciunt. Neque porro quisquam est, qui dolorem ipsum quia dolor sit amet, consectetur, adipisci velit, sed quia non numquam eius modi tempora</p>
  <a class="btn" style="left:504px;top:268px;width:192px;height:42px">Get started now</a>
</section>

<section class="testimonials">
  <h2 class="section-title" style="top:1988px">Client Testimonial</h2>
  <div class="client-photo" style="left:133px;top:2080px" role="img" aria-label="Headshot of a smiling client"></div>
  <p class="quote" style="left:303px;top:2075px">“Lorem ipsum dolor sit amet, consectetur adipiscing elit, sed do eiusmod tempor incididunt ut labore et dolore magna aliqua. Ut enim ad minim veniam,</p>
  <p class="quote-by" style="left:303px;top:2196px">- John Doe -</p>

  <div class="client-photo" style="left:645px;top:2080px" role="img" aria-label="Headshot of a second client"></div>
  <p class="quote" style="left:815px;top:2075px">“Lorem ipsum dolor sit amet, consectetur adipiscing elit, sed do eiusmod tempor incididunt ut labore et dolore magna aliqua. Ut enim ad minim veniam,</p>
  <p class="quote-by" style="left:815px;top:2196px">- John Doe -</p>
</section>

<div class="divider"></div>

<section class="blog">
  <h2 class="section-title" style="top:2320px">Recent Blog</h2>

  <div class="blog-thumb" style="left:133px;top:2407px;background:linear-gradient(135deg,#6f7a86,#c7c0b0 55%,#3e4752)" role="img" aria-label="Video still: team meeting around a table"></div>
  <div class="blog-thumb" style="left:452px;top:2407px;background:linear-gradient(135deg,#dcd8d2,#f2f0ec 50%,#8a6b5a)" role="img" aria-label="Video still: businesswoman in an interview"></div>
  <div class="blog-thumb" style="left:771px;top:2407px;background:linear-gradient(135deg,#eef0f1,#7c93aa 55%,#3d5878)" role="img" aria-label="Video still: woman writing notes at a desk"></div>

  <svg class="abs" style="left:256px;top:2462px" width="52" height="52" viewBox="0 0 52 52"><circle cx="26" cy="26" r="24" fill="rgba(255,255,255,.55)" stroke="rgba(60,60,60,.7)" stroke-width="2"/><path d="M20 15 L37 26 L20 37 Z" fill="#333"/></svg>
  <svg class="abs" style="left:574px;top:2462px" width="52" height="52" viewBox="0 0 52 52"><circle cx="26" cy="26" r="24" fill="rgba(255,255,255,.55)" stroke="rgba(60,60,60,.7)" stroke-width="2"/><path d="M20 15 L37 26 L20 37 Z" fill="#333"/></svg>
  <svg class="abs" style="left:893px;top:2462px" width="52" height="52" viewBox="0 0 52 52"><circle cx="26" cy="26" r="24" fill="rgba(255,255,255,.55)" stroke="rgba(60,60,60,.7)" stroke-width="2"/><path d="M20 15 L37 26 L20 37 Z" fill="#333"/></svg>

  <h3 class="blog-title" style="left:133px;top:2584px">MARCUSFENWOLD</h3>
  <h3 class="blog-title" style="left:452px;top:2584px">MARCUSFENWOLD</h3>
  <h3 class="blog-title" style="left:771px;top:2584px">MARCUSFENWOLD</h3>
  <p class="blog-date" style="left:133px;top:2611px">Feb 02,2017</p>
  <p class="blog-date" style="left:452px;top:2611px">Feb 02,2017</p>
  <p class="blog-date" style="left:771px;top:2611px">Feb 02,2017</p>
</section>

<footer class="site-footer">
  <div class="footer-col" style="left:133px">
    <h4>MENU</h4><hr>
    <ul><li>Home</li><li>About Us</li><li>Solutions</li><li>Blog</li><li>Contact us</li></ul>
  </div>
  <div class="footer-col" style="left:399px">
    <h4>COMPANY</h4><hr>
    <ul><li>Support</li><li>Terms of use</li><li>Privacy policy</li><li>Affiliate Program</li></ul>
  </div>
  <div class="footer-col" style="left:646px">
    <h4>Support</h4><hr>
    <ul><li>Location</li><li>Feedback</li><li>Send Request</li><li>Contact us</li></ul>
  </div>
  <div class="footer-col" style="left:890px">
    <h4>Connect</h4><hr>
    <ul>
      <li><svg width="9" height="9"><circle cx="4.5" cy="4.5" r="4" fill="#fff"/></svg>Friendwall</li>
      <li><svg width="9" height="9"><circle cx="4.5" cy="4.5" r="4" fill="#fff"/></svg>Chirpline</li>
      <li><svg width="9" height="9"><circle cx="4.5" cy="4.5" r="4" fill="#fff"/></svg>RSS</li>
    </ul>
  </div>
  <hr class="footer-rule">
  <p class="copyright">© 2017 marcusfenwold.net. All rights reserved.</p>
</footer>

</body>
</html>
```